High end Electrical/home automation Business Card

Need a card for a high end electrical and home automation company utilising the existing logo.
Phone
Email
Website

Like black look with raised detail. Don’t necessarily need to keep colour of logo it could be made grayscale or white etc

Target Market(s)

High end clients

Contact Information for Business Card

Brightmoor Electrical

Requirements
Must have
• Logo, phone, email, website, address

High end look
Nice to have
• Black background card
Raised font
Should not have
• Lots of colour

```html
<!DOCTYPE html>
<html lang="en">
<head>
<meta charset="utf-8">
<title>Brightmoor Electrical – Business Card</title>
<link rel="stylesheet" href="https://fonts.googleapis.com/css2?family=Montserrat:wght@400;500;800&display=swap">
<style>
  :root {
    --backdrop: #adada8;
    --card: #37373a;
    --card-deep: #2e2e31;
    --accent: #0a8fdc;
    --ink: #f2f2f2;
    --ink-soft: #d8d8d8;
  }
  * { box-sizing: border-box; margin: 0; padding: 0; }
  html, body {
    width: 1200px; height: 801px; overflow: hidden;
    background: var(--backdrop);
    font-family: "Montserrat", Arial, sans-serif;
  }
  .stage {
    position: relative; width: 1200px; height: 801px;
    display: flex; align-items: center; justify-content: center; gap: 48px;
  }
  .card {
    position: relative; width: 525px; height: 300px;
    background: var(--card);
    border-bottom: 4px solid var(--accent);
    box-shadow: 0 14px 28px rgba(0,0,0,.28);
    overflow: hidden;
  }
  /* Front */
  .card-front .brand {
    position: absolute; top: 52px; right: 40px;
    display: flex; align-items: center; gap: 10px;
    font-weight: 800; font-size: 22px; color: var(--ink);
    letter-spacing: -.2px;
  }
  .brand-dot {
    width: 14px; height: 14px; border-radius: 50%; background: var(--accent);
  }
  .card-front .person {
    position: absolute; left: 40px; top: 92px;
  }
  .person-name {
    font-weight: 500; font-size: 22px; letter-spacing: 1.5px;
    color: var(--accent); text-transform: uppercase;
  }
  .person-role {
    font-size: 15px; color: var(--ink); margin-top: 2px;
  }
  .divider {
    position: absolute; left: 40px; right: 40px; top: 158px;
    height: 1px; background: var(--accent);
  }
  .contacts {
    position: absolute; left: 40px; top: 174px;
    list-style: none; font-size: 14px; color: var(--ink); line-height: 1.45;
  }
  .contacts li { display: flex; align-items: center; gap: 8px; }
  .contacts svg { width: 11px; height: 11px; flex: none; }
  .address {
    position: absolute; right: 40px; top: 174px; text-align: left;
    font-size: 14px; color: var(--ink-soft); line-height: 1.45;
    font-style: normal;
  }
  .edge-tab {
    position: absolute; left: 0; bottom: 0; width: 26px; height: 18px;
    background: var(--accent);
  }
  /* Back */
  .card-back {
    background: linear-gradient(160deg, var(--card) 40%, var(--card-deep));
  }
  .card-back .brand {
    position: absolute; left: 40px; bottom: 44px;
    font-weight: 800; font-size: 30px; color: var(--ink);
    letter-spacing: -.3px;
  }
</style>
</head>
<body>
<main class="stage">
  <section class="card card-front" aria-label="Card front">
    <div class="brand"><span class="brand-dot"></span>Brightmoor Electrical</div>
    <div class="person">
      <p class="person-name">Daniel Harlow</p>
      <p class="person-role">Founder</p>
    </div>
    <div class="divider"></div>
    <ul class="contacts">
      <li>
        <svg viewBox="0 0 12 12"><path d="M2 1l2 0 1 3-1.5 1a6 6 0 0 0 3.5 3.5L8 7l3 1 0 2c0 1-1 1.5-2 1.5A9 9 0 0 1 .5 3C.5 2 1 1 2 1z" fill="var(--accent)"/></svg>
        555 014 2837
      </li>
      <li>
        <svg viewBox="0 0 12 12"><rect x=".75" y="2.25" width="10.5" height="7.5" fill="none" stroke="var(--accent)" stroke-width="1.2"/><path d="M1 2.5l5 4 5-4" fill="none" stroke="var(--accent)" stroke-width="1.2"/></svg>
        hello@brightmoor.com
      </li>
      <li>
        <svg viewBox="0 0 12 12"><circle cx="6" cy="6" r="5" fill="none" stroke="var(--accent)" stroke-width="1.2"/><path d="M1 6h10M6 1c-2.5 3-2.5 7 0 10M6 1c2.5 3 2.5 7 0 10" fill="none" stroke="var(--accent)" stroke-width="1"/></svg>
        brightmoorelectrical.com
      </li>
    </ul>
    <address class="address">418 Fenwick Lane<br>Ashvale, WA 99000</address>
    <div class="edge-tab"></div>
  </section>

  <section class="card card-back" aria-label="Card back">
    <div class="brand">Brightmoor Electrical</div>
  </section>
</main>
</body>
</html>
```